Digital Marketing Website Redesign, modern, fresh, dynamic

Hi there, we would like to freshen up our website and create a new dynamic look. We are a digital marketing agency who specialise in digital transformation in the form of creating websites for appointment bookings. Our clients are service businesses such as hairdressers, dentists and doctors who's patients need to book appointments with them.

Our company name is Tallomex with the point being we can help increase your revenue curve by increasing your appointment bookings.

Our services include building the website, creating campaigns to drive traffic, increasing conversions and monitoring and reporting.

We are playing with a tagline of 'Step into your Digital Transformation' as we have a 5 step journey that customers can take with us getting them from zero to full appointment bookings.

Our current website is www.tallomex-sample.com

You can see a draft design that I mocked up on Canva here https://www.draftboard-sample.com/design/QXB82LmpR7T/KpoW39dnFsYbZet_wqe_OPa/edit?utm_content=QXB82LmpR7T&utm_campaign=designshare&utm_medium=link2&utm_source=sharebutton

Also attached some other homepage ideas. In regard to photos we are open to ideas.

Please let if you need any more information to provide us with an initial design. Thanks million and I look forward to receiving fantastic designs :)

Marian Dobbs
Tallomex

Target Market(s)

Appointment based businesses such as hairdressers, dentists, doctors

Industry/Entity Type

Marketing and Digital

Coding

Coded - Design and coding required

Number of Pages Required

1 page

Colors
0094D4
00A9DD
6FCCEA
C7EBF8
E9F6FB

Requirements
Must have
• Appointment booking CTA
Nice to have
• A website we like https://www.fergalwhitty-sample.ie

```html
<!DOCTYPE html>
<html lang="en">
<head>
<meta charset="utf-8">
<title>Tallomex — Step into your Digital Transformation</title>
<link rel="stylesheet" href="https://fonts.googleapis.com/css2?family=Fira+Sans:wght@400;500;600;700&family=Open+Sans:wght@400;600;700&display=swap">
<style>
:root{
  --navy:#1f3d6e;
  --band:#1d3f72;
  --brand:#0094d4;
  --brand-bright:#00a9dd;
  --brand-soft:#6fccea;
  --brand-pale:#c7ebf8;
  --brand-mist:#e9f6fb;
  --ink:#1b3c6e;
  --body:#5b6270;
  --dark:#1c2a3d;
  --footer:#1b2233;
  --bar:#253a62;
  --white:#ffffff;
  --teal:#00a9dd;
}
*{margin:0;padding:0;box-sizing:border-box}
html,body{width:1200px;height:5121px;overflow:hidden;background:var(--white)}
body{position:relative;font-family:"Open Sans",Arial,sans-serif;color:var(--body)}
.abs{position:absolute}
.heading{font-family:"Fira Sans",Arial,sans-serif;font-weight:600;color:var(--ink);line-height:1.35}
.eyebrow{font-family:"Fira Sans",Arial,sans-serif;font-size:15px;color:var(--brand);font-weight:500}
.center{left:0;width:1200px;text-align:center}
.para{font-size:12.5px;line-height:22px;color:var(--body)}
.btn{display:flex;align-items:center;justify-content:center;gap:12px;background:var(--brand);color:#fff;font-size:10px;font-weight:700;font-family:"Fira Sans",sans-serif;letter-spacing:.3px;border-radius:3px;white-space:nowrap}
.photo{border-radius:4px}

/* hero */
.hero{left:0;top:0;width:1200px;height:700px;background:linear-gradient(120deg,#07142a 0%,#123357 40%,#1c4f78 65%,#0d2744 100%)}
.nav{left:358px;top:0;width:477px;height:56px;background:#fff;border-radius:0 0 26px 26px;display:flex;justify-content:space-around;align-items:center;padding:0 24px;font-size:10.5px;font-weight:600;color:var(--navy)}
.brand{font-family:"Fira Sans",sans-serif;font-weight:700;font-size:26px;color:#fff}
.social{width:26px;height:26px;border:1.5px solid #fff;border-radius:50%;left:49px}
.hero-title{left:228px;top:205px;font-family:"Fira Sans",sans-serif;font-weight:600;font-size:46px;line-height:60px;color:#fff}

/* services */
.svc-box{background:rgba(29,63,114,.93);color:#fff;text-align:center;padding:36px 22px 0;border-radius:3px}
.svc-box h3{font-family:"Fira Sans",sans-serif;font-weight:500;font-size:24px;line-height:33px;margin-bottom:14px}
.svc-box p{font-size:12px;line-height:21px}
.circle-arrow{width:32px;height:32px;border:2px solid #fff;border-radius:50%;margin:12px auto 0;display:flex;align-items:center;justify-content:center}

/* success */
.feat-title{font-family:"Fira Sans",sans-serif;font-size:16px;font-weight:500;color:#fff}
.feat-body{font-size:12px;line-height:22px;color:#fff}
.feat-icon{width:68px;height:68px;border:1.5px solid #fff;border-radius:50%;display:flex;align-items:center;justify-content:center}

/* quote */
.field{border:1px solid #8b95a6;border-radius:3px;font-size:9px;color:#aab;padding:8px 14px}

/* footer */
.footer{left:0;top:4540px;width:1200px;height:581px;background:var(--footer)}
.f-head{font-family:"Fira Sans",sans-serif;font-weight:600;font-size:21px;color:#fff}
.f-line{height:3px;width:42px;background:var(--brand-bright)}
.f-links{list-style:none;font-size:13.5px;color:#fff}
.f-links li{height:30.5px;display:flex;align-items:center;gap:12px}
.f-links li::before{content:"›";font-size:18px;line-height:1}
.bar-label{font-size:13px;font-weight:700;color:#fff}
.bar-value{font-size:14px;color:#fff}
.legal{font-size:12px;color:#6a7184}
</style>
</head>
<body>

<!-- HERO -->
<div class="abs hero" role="img" aria-label="Photo: business man and woman reviewing a tablet in front of a glowing digital tunnel with a person walking"></div>
<svg class="abs" style="left:0;top:600px" width="1200" height="100" viewBox="0 0 1200 100"><path d="M0,76 L370,76 C415,76 425,7 480,7 L1200,7 L1200,100 L0,100Z" fill="#fff"/></svg>
<div class="abs brand" style="left:129px;top:28px">Tallomex</div>
<nav class="abs nav"><span>HOME</span><span>ABOUT</span><span>SERVICES</span><span>CASES</span><span>BLOG</span><span>CONTACT ⌄</span></nav>
<div class="abs" style="left:904px;top:16px;display:flex;gap:10px;align-items:center;color:#fff">
  <svg width="20" height="20" viewBox="0 0 24 24"><path d="M6 3l3 0 2 5-2.5 1.5a11 11 0 0 0 6 6L16 13l5 2v3a2 2 0 0 1-2 2A16 16 0 0 1 4 5a2 2 0 0 1 2-2z" fill="none" stroke="#fff" stroke-width="1.6"/></svg>
  <div style="line-height:12px"><div style="font-size:7.5px">Have Any Questions?</div><div style="font-size:10px;font-weight:600">+01 3 5550 1942</div></div>
</div>
<div class="abs social" style="top:268px"></div>
<div class="abs social" style="top:311px"></div>
<div class="abs social" style="top:353px;background:var(--brand-bright);border-color:var(--brand-bright)"></div>
<div class="abs social" style="top:394px"></div>
<h1 class="abs hero-title">Step into your<br>Digital Transformation</h1>
<p class="abs" style="left:234px;top:342px;width:440px;font-size:13px;line-height:21px;color:#fff">Lorem ipsum dolor sit amet, consectetur adipiscing elit, sed do eiusmod tempor incididunt ut labore et dolore magna aliqua.</p>
<div class="abs btn" style="left:234px;top:401px;width:190px;height:44px">BOOK AN APPOINTMENT <span style="font-size:14px">→</span></div>

<!-- ABOUT -->
<div class="abs eyebrow" style="left:117px;top:820px">About Us</div>
<h2 class="abs heading" style="left:117px;top:840px;font-size:34px;line-height:46px">Empower. Transform.<br>Thrive</h2>
<p class="abs para" style="left:123px;top:938px;width:420px">Lorem ipsum dolor sit amet, consectetur adipiscing elit, sed do eiusmod tempor incididunt ut labore et dolore magna aliqua. Ut enim ad minim veniam, q</p>
<p class="abs" style="left:123px;top:1022px;font-size:17px;line-height:26px;color:var(--brand-bright)">"Navigate Challenges, Embrace<br>Opportunities"</p>
<div class="abs photo" style="left:572px;top:791px;width:524px;height:401px;background:linear-gradient(135deg,#dfe2e4,#b8b2a8 60%,#8c8378)" role="img" aria-label="Photo: smiling businesswoman holding a tablet in a bright office"></div>
<div class="abs" style="left:1119px;top:791px;width:4px;height:123px;background:var(--brand-bright)"></div>
<div class="abs photo" style="left:121px;top:1099px;width:326px;height:220px;background:linear-gradient(135deg,#3b6fa8,#c9a88a 55%,#e9e3dc)" role="img" aria-label="Photo: woman presenting charts on a laptop to colleagues"></div>
<div class="abs photo" style="left:475px;top:1099px;width:326px;height:220px;background:linear-gradient(135deg,#d8d2c6,#6f7b86 60%,#1e2630)" role="img" aria-label="Photo: two professionals discussing documents at a table"></div>

<!-- SERVICES -->
<div class="abs" style="left:0;top:1407px;width:1200px;height:709px;background:var(--brand-mist)"></div>
<div class="abs eyebrow center" style="top:1470px">Our Latest Services</div>
<h2 class="abs heading center" style="top:1497px;font-size:34px">Services We Provide</h2>
<div class="abs photo" style="left:93px;top:1596px;width:320px;height:401px;background:linear-gradient(160deg,#e4e7ea,#8f9aa6 55%,#3c4856)" role="img" aria-label="Photo: hand touching digital document and cloud icons"></div>
<div class="abs photo" style="left:439px;top:1635px;width:320px;height:402px;background:linear-gradient(160deg,#5a6675,#1c2430 60%,#c9cdd2)" role="img" aria-label="Photo: businessman in a suit using a smartphone"></div>
<div class="abs photo" style="left:789px;top:1596px;width:320px;height:401px;background:radial-gradient(circle at 50% 45%,#8fb3cf,#2c4966 50%,#1d2c3d)" role="img" aria-label="Photo: hands holding a glowing globe"></div>
<div class="abs svc-box" style="left:121px;top:1810px;width:264px;height:227px"><h3>Marketing<br>Services</h3><p>Lorem ipsum dolor sit amet, ae consectetur adipiscing</p><div class="circle-arrow"><svg width="12" height="12" viewBox="0 0 12 12"><path d="M4 2l4 4-4 4" fill="none" stroke="#fff" stroke-width="2"/></svg></div></div>
<div class="abs svc-box" style="left:467px;top:1596px;width:264px;height:224px;padding-top:30px"><h3>Online<br>Booking Apps</h3><p>Lorem ipsum dolor sit amet, ae consectetur adipiscing</p><div class="circle-arrow"><svg width="12" height="12" viewBox="0 0 12 12"><path d="M4 2l4 4-4 4" fill="none" stroke="#fff" stroke-width="2"/></svg></div></div>
<div class="abs svc-box" style="left:815px;top:1810px;width:266px;height:227px"><h3>Services<br>Marketing</h3><p>Lorem ipsum dolor sit amet, ae consectetur adipiscing</p><div class="circle-arrow"><svg width="12" height="12" viewBox="0 0 12 12"><path d="M4 2l4 4-4 4" fill="none" stroke="#fff" stroke-width="2"/></svg></div></div>

<!-- SUCCESS STORY -->
<div class="abs" style="left:0;top:2178px;width:600px;height:495px;background:var(--band)"></div>
<div class="abs" style="left:600px;top:2146px;width:600px;height:560px;background:linear-gradient(160deg,#0094d4 0%,#00a9dd 55%,#6fccea 100%)" role="img" aria-label="Bright blue backdrop with faint glowing data bars"></div>
<div class="abs eyebrow" style="left:117px;top:2279px;color:var(--brand-soft)">Why we are the Best</div>
<h2 class="abs" style="left:117px;top:2302px;font-family:'Fira Sans',sans-serif;font-weight:600;font-size:34px;line-height:46px;color:#fff">Your Success Story<br>Starts Here</h2>
<p class="abs para" style="left:123px;top:2414px;width:420px;color:#fff">Lorem ipsum dolor sit amet, consectetur adipiscing elit, sed do eiusmod tempor incididunt ut labore et dolore magna aliqua. Ut enim ad minim veniam, q</p>
<div class="abs btn" style="left:127px;top:2530px;width:151px;height:43px">READ MORE <span style="font-size:14px">→</span></div>
<div class="abs" style="left:558px;top:2237px;width:475px;height:388px;border:3px solid #fff"></div>
<div class="abs" style="left:1033px;top:2237px;width:40px;height:148px;background:#fff;display:flex;align-items:center;justify-content:center"><span style="transform:rotate(-90deg);white-space:nowrap;font-size:12px;font-weight:600;color:var(--navy);text-decoration:underline">GET A QUOTE</span></div>
<div class="abs feat-icon" style="left:650px;top:2275px"><svg width="30" height="30" viewBox="0 0 30 30" fill="none" stroke="#fff" stroke-width="1.6"><circle cx="15" cy="10" r="5"/><path d="M5 26c2-6 18-6 20 0"/></svg></div>
<div class="abs feat-icon" style="left:650px;top:2386px"><svg width="30" height="30" viewBox="0 0 30 30" fill="none" stroke="#fff" stroke-width="1.6"><path d="M15 4l3 7 7 1-5 5 1 8-6-4-6 4 1-8-5-5 7-1z"/></svg></div>
<div class="abs feat-icon" style="left:650px;top:2498px"><svg width="30" height="30" viewBox="0 0 30 30" fill="none" stroke="#fff" stroke-width="1.6"><path d="M5 22a10 10 0 1 1 20 0"/><path d="M15 22l5-8"/></svg></div>
<div class="abs" style="left:743px;top:2278px;width:260px"><div class="feat-title">Customized Solutions</div><div class="feat-body">Lorem ipsum dolor sit amet, consecte tur adipiscing elit, sed do</div></div>
<div class="abs" style="left:743px;top:2390px;width:260px"><div class="feat-title">Client-Centric</div><div class="feat-body">Lorem ipsum dolor sit amet, consecte tur adipiscing elit, sed do</div></div>
<div class="abs" style="left:743px;top:2501px;width:260px"><div class="feat-title">Professionalism</div><div class="feat-body">Lorem ipsum dolor sit amet, consecte tur adipiscing elit, sed do</div></div>

<!-- GALLERY -->
<div class="abs eyebrow center" style="top:2782px">Gallery</div>
<h2 class="abs heading center" style="top:2808px;font-size:34px">Watch Our Videos</h2>
<div class="abs" style="left:93px;top:2907px;width:235px;height:372px;clip-path:polygon(0 14%,100% 0,100% 100%,0 86%);background:linear-gradient(135deg,#c5c9cf,#7b858f)" role="img" aria-label="Video thumbnail: team working at laptops"></div>
<div class="abs" style="left:354px;top:2907px;width:496px;height:372px;background:linear-gradient(135deg,#2a3b4d,#4d5e6e 45%,#8e3b44 70%,#2b3642)" role="img" aria-label="Video thumbnail: hands on a laptop with charts"></div>
<div class="abs" style="left:876px;top:2907px;width:231px;height:372px;clip-path:polygon(0 0,100% 14%,100% 86%,0 100%);background:linear-gradient(225deg,#c5c9cf,#7b858f)" role="img" aria-label="Video thumbnail: team working at laptops"></div>
<div class="abs" style="left:556px;top:3056px;width:76px;height:76px;border-radius:50%;background:var(--teal);display:flex;align-items:center;justify-content:center"><svg width="30" height="32" viewBox="0 0 30 32"><path d="M6 2l22 14-22 14z" fill="#fff"/></svg></div>
<p class="abs" style="left:391px;top:3198px;font-size:16px;line-height:25px;color:#fff">Lorem ipsum dolor sit amet, consecteturipsum<br>dolor sit amet, consectetur</p>

<!-- QUOTE -->
<div class="abs" style="left:0;top:3358px;width:455px;height:580px;background:var(--brand)"></div>
<div class="abs" style="left:455px;top:3358px;width:745px;height:580px;background:var(--dark)"></div>
<div class="abs" style="left:119px;top:3388px;width:477px;height:550px;background:linear-gradient(180deg,#6c7785 0%,#2a3444 60%,#1c2a3d 100%);clip-path:polygon(20% 0,85% 4%,100% 30%,100% 100%,0 100%,5% 25%)" role="img" aria-label="Photo: smiling businessman and businesswoman standing back to back"></div>
<div class="abs" style="left:0;top:3839px;width:586px;height:1px;background:#fff"></div>
<div class="abs" style="left:819px;top:3839px;width:381px;height:1px;background:#fff"></div>
<div class="abs" style="left:934px;top:3453px;width:266px;height:1px;background:#fff"></div>
<div class="abs" style="left:56px;top:3815px;transform-origin:0 0;transform:rotate(-90deg);font-family:'Fira Sans',sans-serif;font-weight:700;font-size:34px;line-height:40px;color:#fff;white-space:nowrap">GET A FREE QUOTE</div>
<div class="abs eyebrow" style="left:630px;top:3430px;color:var(--brand-soft)">Contact Us</div>
<h2 class="abs" style="left:630px;top:3455px;font-family:'Fira Sans',sans-serif;font-weight:600;font-size:31px;color:#fff">GET A FREE QUOTE</h2>
<div class="abs field" style="left:634px;top:3539px;width:205px;height:32px">Your Name</div>
<div class="abs field" style="left:866px;top:3539px;width:205px;height:32px">Phone Number</div>
<div class="abs field" style="left:634px;top:3598px;width:205px;height:32px">Email Address</div>
<div class="abs field" style="left:866px;top:3598px;width:205px;height:32px">Location</div>
<div class="abs field" style="left:634px;top:3656px;width:437px;height:131px">Your Message</div>
<div class="abs btn" style="left:626px;top:3821px;width:180px;height:42px">BOOK APPOINTMENT <span style="font-size:14px">→</span></div>

<!-- TESTIMONIALS -->
<div class="abs eyebrow center" style="top:4037px">Our Testimonials</div>
<h2 class="abs heading center" style="top:4063px;font-size:34px">Client Reviews</h2>
<div class="abs" style="left:99px;top:4149px;width:137px;height:286px;background:linear-gradient(180deg,#5776a6,#2c4a7c)" role="img" aria-label="Photo: previous client portrait"></div>
<div class="abs" style="left:260px;top:4149px;width:227px;height:286px;background:linear-gradient(180deg,#eef0f2,#9aa2ad 70%,#5b6572)" role="img" aria-label="Photo: smiling client with glasses"></div>
<div class="abs" style="left:487px;top:4149px;width:451px;height:286px;background:#fff;box-shadow:0 4px 18px rgba(0,0,0,.08)"></div>
<div class="abs" style="left:962px;top:4149px;width:137px;height:286px;background:linear-gradient(180deg,#5776a6,#2c4a7c)" role="img" aria-label="Photo: next client portrait"></div>
<svg class="abs" style="left:152px;top:4278px" width="32" height="28" viewBox="0 0 32 28"><path d="M30 14H4M14 4L4 14l10 10" fill="none" stroke="#fff" stroke-width="2.4"/></svg>
<svg class="abs" style="left:1015px;top:4278px" width="32" height="28" viewBox="0 0 32 28"><path d="M2 14h26M18 4l10 10-10 10" fill="none" stroke="#fff" stroke-width="2.4"/></svg>
<div class="abs" style="left:531px;top:4188px;font-family:'Fira Sans',sans-serif;font-weight:700;font-size:48px;line-height:48px;color:var(--navy)">“</div>
<p class="abs para" style="left:530px;top:4236px;width:370px">Lorem ipsum dolor sit amet, consectetur adipiscing elit, sed do eiusmod tempor incididunt ut labore et dolore magna aliqua. Ut enim ad minim veniam, qdidunt ut labore et dolore magna aliqua.</p>
<div class="abs" style="left:532px;top:4343px;font-size:17px;font-weight:600;color:#222">Nora Pell</div>
<div class="abs" style="left:532px;top:4372px;font-size:10px;color:#999">Chairperson</div>
<div class="abs" style="left:825px;top:4344px;font-size:14px;letter-spacing:2px;color:#f07a22">★★★★★</div>

<!-- FOOTER -->
<footer class="abs footer"></footer>
<div class="abs" style="left:83px;top:4626px;font-family:'Fira Sans',sans-serif;font-weight:700;font-size:40px;color:#2f67b4">Tallomex</div>
<div class="abs" style="left:83px;top:4702px;font-size:17px;font-weight:700;color:#fff">800-555-0142</div>
<div class="abs" style="left:83px;top:4732px;font-size:13px;font-weight:700;color:#fff">Call for free consultation</div>
<p class="abs" style="left:83px;top:4769px;width:280px;font-size:12.5px;line-height:23px;color:#fff">Lorem ipsum dolor sit amet, consectet sed do eiusmod tempor incididunt ut la magna aliqua. Ut enim</p>
<div class="abs" style="left:83px;top:4856px;font-size:14px;font-weight:700;color:#fff">Read more &nbsp;›</div>

<div class="abs f-head" style="left:437px;top:4630px">Useful Links</div>
<div class="abs f-line" style="left:437px;top:4668px"></div>
<ul class="abs f-links" style="left:443px;top:4698px"><li>About Company</li><li>Leadership</li><li>Blog Post</li><li>FAQ'S</li><li>Certification</li><li>Testimonials</li></ul>
<ul class="abs f-links" style="left:605px;top:4698px"><li>Services</li><li>Industries</li><li>Feedback</li><li>Partners</li><li>Pricing</li><li>Contct</li></ul>

<div class="abs f-head" style="left:789px;top:4630px">Newsletter</div>
<div class="abs f-line" style="left:789px;top:4668px"></div>
<p class="abs" style="left:787px;top:4722px;width:320px;font-size:12px;line-height:24px;color:#fff">Dont miss to subscribe to our news feeds, kindly fill the form below</p>
<div class="abs" style="left:789px;top:4797px;width:266px;height:47px;background:#232b3e;border-radius:24px 0 0 24px;font-size:12px;color:#fff;padding:15px 24px">Your Email Address</div>
<div class="abs" style="left:1055px;top:4797px;width:52px;height:47px;background:var(--brand);border-radius:0 24px 24px 0;display:flex;align-items:center;justify-content:center"><svg width="14" height="16" viewBox="0 0 14 16"><path d="M3 2l7 6-7 6" fill="none" stroke="#fff" stroke-width="2.4"/></svg></div>

<div class="abs" style="left:85px;top:4971px;width:1028px;height:86px;background:var(--bar);border-radius:4px"></div>
<div class="abs" style="left:427px;top:4990px;width:1px;height:48px;background:#4b5d84"></div>
<div class="abs" style="left:771px;top:4990px;width:1px;height:48px;background:#4b5d84"></div>
<svg class="abs" style="left:113px;top:4999px" width="28" height="30" viewBox="0 0 28 30" fill="none" stroke="#6fccea" stroke-width="2"><path d="M14 28s9-9 9-16a9 9 0 0 0-18 0c0 7 9 16 9 16z"/><circle cx="14" cy="12" r="3.5"/></svg>
<svg class="abs" style="left:456px;top:5000px" width="30" height="28" viewBox="0 0 30 28" fill="none" stroke="#6fccea" stroke-width="2"><rect x="3" y="3" width="24" height="18" rx="2"/><path d="M8 10h14M8 15h10M8 21l-3 5"/></svg>
<svg class="abs" style="left:796px;top:5000px" width="30" height="28" viewBox="0 0 30 28" fill="none" stroke="#6fccea" stroke-width="2"><path d="M27 2L2 12l10 4 4 10z"/><path d="M12 16L27 2"/></svg>
<div class="abs" style="left:165px;top:4994px"><div class="bar-label">Location</div><div class="bar-value">246 &nbsp;Rd, Country</div></div>
<div class="abs" style="left:507px;top:4994px"><div class="bar-label">Mail us</div><div class="bar-value">hello@tallomex-sample.com</div></div>
<div class="abs" style="left:848px;top:4994px"><div class="bar-label">Office hrs</div><div class="bar-value">9.00am to 7.00pm (Mon-Sat)</div></div>

<div class="abs legal" style="left:85px;top:5081px">Tallomex</div>
<div class="abs legal" style="left:801px;top:5081px">Privacy Policy</div>
<div class="abs legal" style="left:912px;top:5081px">Terms &amp; Conditions</div>
<div class="abs legal" style="left:1055px;top:5081px">Site Map</div>
<div class="abs" style="left:1125px;top:5027px;width:47px;height:47px;background:var(--brand);border-radius:3px;display:flex;align-items:center;justify-content:center"><svg width="16" height="12" viewBox="0 0 16 12"><path d="M2 10l6-6 6 6" fill="none" stroke="#fff" stroke-width="2.4"/></svg></div>

</body>
</html>
```